Presentation Box for dry goods meat product

We would like a box designed for presentation on a shelf. Our product is fully cooked meats (beef, pork and chicken) that has a 12- to 18-month shelf-life without refrigeration. It's not dried food, but because of the cooking process it's succulent meat in sauce, storable at room temperature.Our anchor product will be "Timber Hollow Smoke Pot."The dimensions for the box will be approximately 8" tall by 5" wide and 2.5" deep.We have an oval-shaped (horizontal) logo in Navy, Crimson and Old Gold (think Dunmore Lanterns colors).
Updates

Reason: We haven't received enough options. We want the design to say "Timber Hollow Style Smoke Pot" not "Timber Hollow Smoke Pot." Use pictures of beef brisket (not steaks), pulled pork (not pork chops) and pulled chicken (not chicken legs/thighs).

Target Market(s)

Meat-buying consumers

Industry/Entity Type

Cooking

Requirements
Must have
• Space for ingredients and nutrition information. The name of our company is Merrow Foods.
Nice to have
• Picture of Bar-B-Que beef, pork and chicken

```html
<!DOCTYPE html>
<html lang="en">
<head>
<meta charset="utf-8">
<title>Merrow Foods – Timber Hollow Style Smoke Pot Box Panels</title>
<link rel="stylesheet" href="https://fonts.googleapis.com/css2?family=Playfair+Display:wght@900&family=Roboto:wght@400;700;900&display=swap">
<style>
  :root {
    --bg: #ffffff;
    --brown-dark: #4a2a0e;
    --brown: #6e4118;
    --brown-light: #8a5423;
    --cream: #f6e7b6;
    --gold: #ffe23a;
    --yellow-panel: #f4e9a6;
    --navy: #14306b;
    --pork: #1f6fb8;
    --chicken: #e8861a;
    --brisket: #c8176f;
    --ink: #2a1a08;
    --white: #ffffff;
  }
  * { box-sizing: border-box; margin: 0; padding: 0; }
  html, body { width: 1200px; height: 636px; overflow: hidden; background: var(--bg); }
  body { font-family: "Roboto", sans-serif; }

  .lineup {
    width: 1200px; height: 636px;
    display: flex; align-items: center; justify-content: center; gap: 34px;
  }
  .box { display: flex; height: 400px; box-shadow: 0 8px 16px rgba(0,0,0,.2); }

  .face, .side {
    position: relative; height: 400px; overflow: hidden;
    background: linear-gradient(180deg, var(--brown-light) 0%, var(--brown) 45%, var(--brown-dark) 100%);
  }
  .face { width: 200px; }
  .side { width: 64px; }
  .side-left { box-shadow: inset -6px 0 8px rgba(0,0,0,.25); }
  .side-right { box-shadow: inset 6px 0 8px rgba(0,0,0,.25); }

  /* brand oval */
  .brand {
    position: absolute; top: 14px; left: 50%; transform: translateX(-50%);
    width: 136px; height: 54px; border-radius: 50%;
    background: var(--white); display: flex; align-items: center; justify-content: center;
  }
  .brand-name { font-weight: 900; font-size: 17px; color: var(--navy); white-space: nowrap; }

  /* title */
  .title { position: absolute; top: 80px; left: 0; right: 0; text-align: center; color: var(--cream); font-family: "Playfair Display", serif; font-weight: 900; text-transform: uppercase; line-height: 1; }
  .title-small { display: block; font-size: 13px; letter-spacing: .3px; }
  .title-large { display: block; font-size: 30px; margin-top: 3px; }

  /* flavour band */
  .band { position: absolute; top: 134px; left: 0; width: 200px; height: 64px; }
  .band-label { position: absolute; top: 152px; left: 14px; color: var(--white); font-size: 11.5px; font-weight: 700; white-space: nowrap; }
  .pork .band-fill { fill: var(--pork); }
  .chicken .band-fill { fill: var(--chicken); }
  .brisket .band-fill { fill: var(--brisket); }
  .band-stripe { fill: var(--gold); }

  /* photo area */
  .photo { position: absolute; top: 192px; left: 0; width: 200px; height: 208px; }
  .pork .photo { background: radial-gradient(ellipse at 55% 55%, #7a3a1c 0%, #5a2a12 45%, #c7a56b 80%, #e9d9b4 100%); }
  .chicken .photo { background: radial-gradient(ellipse at 50% 50%, #b8461e 0%, #8e3014 40%, #e2b97c 75%, #f3ead8 100%); }
  .brisket .photo { background: radial-gradient(ellipse at 45% 45%, #d9b2a8 0%, #c79a8e 45%, #eae3da 80%, #f6f3ee 100%); }

  .net-wt {
    position: absolute; left: 0; bottom: 0; padding: 3px 8px 3px 6px;
    background: var(--gold); color: var(--ink); font-size: 8.5px; font-weight: 700;
  }

  /* side panels with vertical product name */
  .side-band {
    position: absolute; top: 0; bottom: 0; left: 50%; width: 36px; transform: translateX(-50%);
    border-left: 5px solid var(--gold); border-right: 5px solid var(--gold);
    display: flex; align-items: center; justify-content: center;
  }
  .pork .side-band, .back .side-band { background: var(--pork); }
  .chicken .side-band { background: var(--chicken); }
  .brisket .side-band { background: var(--brisket); }
  .vertical {
    writing-mode: vertical-rl; transform: rotate(180deg);
    color: var(--white); font-size: 13.5px; font-weight: 700; white-space: nowrap;
  }

  /* pork side: brand and title turned on end */
  .side-title {
    position: absolute; inset: 0; display: flex; flex-direction: column; align-items: center; justify-content: flex-start;
    padding-top: 24px; writing-mode: vertical-rl;
  }
  .side-brand {
    width: 44px; height: 104px; border-radius: 50%; background: var(--white);
    display: flex; align-items: center; justify-content: center;
  }
  .side-brand .brand-name { font-size: 13px; }
  .side-heading { margin-top: 10px; color: var(--cream); font-family: "Playfair Display", serif; font-weight: 900; text-transform: uppercase; line-height: 1; }
  .side-heading .title-small { font-size: 9.5px; }
  .side-heading .title-large { font-size: 20px; margin-top: 2px; }
  .batch {
    position: absolute; left: 0; right: 0; bottom: 0; height: 110px; background: var(--white);
    padding: 10px 6px; font-size: 7px; line-height: 1.6; color: var(--ink);
  }

  /* back face */
  .back-face { background: linear-gradient(180deg, var(--yellow-panel), #efe08c); }
  .back-face .photo { top: 0; height: 118px; background: linear-gradient(135deg, #b4541e 0%, #6a2f12 50%, #5a7a2a 100%); }
  .back-brand { position: absolute; top: 100px; left: 10px; width: 84px; height: 36px; border-radius: 50%; background: var(--white); display: flex; align-items: center; justify-content: center; box-shadow: 0 1px 3px rgba(0,0,0,.25); }
  .back-brand .brand-name { font-size: 11px; }
  .back-title { position: absolute; top: 122px; left: 100px; color: var(--brown); font-family: "Playfair Display", serif; font-weight: 900; text-transform: uppercase; line-height: 1; }
  .back-title .title-small { font-size: 7px; }
  .back-title .title-large { font-size: 15px; margin-top: 1px; }
  .back-copy { position: absolute; top: 150px; left: 12px; right: 12px; font-size: 8.5px; line-height: 1.35; color: var(--ink); }
  .back-copy strong { font-weight: 700; }
  .ingredients { margin-top: 6px; }
  .ingredients h3 { font-size: 8.5px; font-weight: 700; }
  .info-boxes { position: absolute; left: 12px; right: 12px; top: 250px; bottom: 14px; display: flex; gap: 6px; }
  .info-box { flex: 1; background: var(--white); border: 1px solid #c9b777; padding: 5px; font-size: 8px; font-weight: 700; color: var(--ink); }
</style>
</head>
<body>
<main class="lineup">

  <article class="box back" aria-label="Back and side of pulled pork box">
    <div class="side side-left">
      <div class="side-band"><span class="vertical">Bar-B-Que Pulled Pork</span></div>
    </div>
    <section class="face back-face">
      <div class="photo" role="img" aria-label="Photo of barbecue pulled pork with baked beans and green onion"></div>
      <div class="back-brand"><span class="brand-name">Merrow Foods</span></div>
      <div class="back-title"><span class="title-small">Timber Hollow Style</span><span class="title-large">Smoke Pot</span></div>
      <div class="back-copy">
        <p><strong>Timber Hollow Smoke Pot</strong> is slow cooked tender meat in a rich smoky sauce, ready to heat and serve any day of the week.</p>
        <div class="ingredients">
          <h3>Ingredients :</h3>
          <p>Chicken, Sugar, Salt, Garlic, Tomato Sauce, Vinegar, Spices.</p>
        </div>
      </div>
      <div class="info-boxes">
        <div class="info-box">NUTRITION INFO</div>
        <div class="info-box">SERVING</div>
      </div>
    </section>
  </article>

  <article class="box pork" aria-label="Pulled pork box">
    <div class="side side-left">
      <div class="side-title">
        <div class="side-brand"><span class="brand-name">Merrow Foods</span></div>
        <div class="side-heading"><span class="title-small">Timber Hollow Style</span><span class="title-large">Smoke Pot</span></div>
      </div>
      <div class="batch">Best Before :<br>Batch No :</div>
    </div>
    <section class="face">
      <div class="brand"><span class="brand-name">Merrow Foods</span></div>
      <h1 class="title"><span class="title-small">Timber Hollow Style</span><span class="title-large">Smoke Pot</span></h1>
      <div class="photo" role="img" aria-label="Photo of barbecue pulled pork sandwich with baked beans"></div>
      <svg class="band" viewBox="0 0 250 70" preserveAspectRatio="none" aria-hidden="true">
        <path class="band-stripe" d="M0 16 Q125 -2 250 6 L250 14 Q125 8 0 24Z"/>
        <path class="band-fill" d="M0 24 Q125 8 250 14 L250 44 Q125 40 0 56Z"/>
        <path class="band-stripe" d="M0 56 Q125 40 250 44 L250 50 Q125 48 0 62Z"/>
      </svg>
      <div class="band-label">Bar-B-Que Pulled Pork</div>
      <div class="net-wt">Net Wt. 510g / 18 oz.</div>
    </section>
  </article>

  <article class="box chicken" aria-label="Pulled chicken box">
    <section class="face">
      <div class="brand"><span class="brand-name">Merrow Foods</span></div>
      <h2 class="title"><span class="title-small">Timber Hollow Style</span><span class="title-large">Smoke Pot</span></h2>
      <div class="photo" role="img" aria-label="Photo of barbecue pulled chicken on a bun"></div>
      <svg class="band" viewBox="0 0 250 70" preserveAspectRatio="none" aria-hidden="true">
        <path class="band-stripe" d="M0 16 Q125 -2 250 6 L250 14 Q125 8 0 24Z"/>
        <path class="band-fill" d="M0 24 Q125 8 250 14 L250 44 Q125 40 0 56Z"/>
        <path class="band-stripe" d="M0 56 Q125 40 250 44 L250 50 Q125 48 0 62Z"/>
      </svg>
      <div class="band-label">Bar-B-Que Pulled Chicken</div>
      <div class="net-wt">Net Wt. 510g / 18 oz.</div>
    </section>
    <div class="side side-right">
      <div class="side-band"><span class="vertical">Bar-B-Que Pulled Chicken</span></div>
    </div>
  </article>

  <article class="box brisket" aria-label="Beef brisket box">
    <section class="face">
      <div class="brand"><span class="brand-name">Merrow Foods</span></div>
      <h2 class="title"><span class="title-small">Timber Hollow Style</span><span class="title-large">Smoke Pot</span></h2>
      <div class="photo" role="img" aria-label="Photo of sliced beef brisket with parsley and cucumber"></div>
      <svg class="band" viewBox="0 0 250 70" preserveAspectRatio="none" aria-hidden="true">
        <path class="band-stripe" d="M0 16 Q125 -2 250 6 L250 14 Q125 8 0 24Z"/>
        <path class="band-fill" d="M0 24 Q125 8 250 14 L250 44 Q125 40 0 56Z"/>
        <path class="band-stripe" d="M0 56 Q125 40 250 44 L250 50 Q125 48 0 62Z"/>
      </svg>
      <div class="band-label">Bar-B-Que Beef Brisket</div>
      <div class="net-wt">Net Wt. 510g / 18 oz.</div>
    </section>
    <div class="side side-right">
      <div class="side-band"><span class="vertical">Bar-B-Que Beef Brisket</span></div>
    </div>
  </article>

</main>
</body>
</html>
```